New, modern business card for growing audiology practice

We need a new business card for our audiology practice. Our logo and website have recently changed (more modern) and we want our business cards to reflect this change.
We conduct hearing tests, perform earwax removals, and fit & dispense hearing aids to our patients. We are a family owned practice in which the owner is the one who works directly with the patient. I have attached logos in various formats to use, as well as two ideas I found on this website; as well as a scanned copy of our current logo. Good luck!

Industry/Entity Type

Business

Contact Information for Business Card

Company name: Tolvera Hearing Center
Provider name: Peter Wolstenby, Au.D. F/NSB
Phone number: (440) 683-5127
Address: 837 W. Lindell Ave. Bellmont Falls, OH 44871
email: tolverahearing@postvane.com
website: tolverahearing.com

Colors
000000
aaaaaa
dbdbdb
cacaca
9bcb3c
afd23c
cadf82
b1b1b1

Requirements
Must have
• My card must include information in the "details" section. In the attached images, I found a few that I liked and I would like to model after - "brisky bouncin'" and "Sound Method Center".
• Must be horizontal.
• Must include logos provided. I uploaded them in various file formats and various ways.
• Must match logo font, if possible, if not, please get as close as you can.
Nice to have
• I really like the idea of having a color on one side with just the logo and company name and the contact information and provider name on the other side. I also really like the idea of having the main color dominating on the logo/company side with accent of that same color on the contact side of the card.
Should not have
• Must not be vertical.

```html
<!DOCTYPE html>
<html lang="en">
<head>
<meta charset="utf-8">
<title>Tolvera Hearing Center – Business Card</title>
<link rel="stylesheet" href="https://fonts.googleapis.com/css2?family=Lato:wght@400;700&family=Oswald:wght@500&family=Work+Sans:wght@400&display=swap">
<style>
  :root {
    --black: #0d0d0d;
    --white: #ffffff;
    --green: #6ea532;
    --green-light: #9bcb3c;
    --ink: #222222;
    --grey: #555555;
    --stage: #2a2a2a;
  }
  * { box-sizing: border-box; margin: 0; padding: 0; }
  html, body { width: 1200px; height: 900px; overflow: hidden; }
  body {
    background: var(--stage);
    display: flex;
    flex-direction: column;
    align-items: center;
    justify-content: center;
    gap: 36px;
  }
  .card {
    width: 700px;
    height: 400px;
    position: relative;
    box-shadow: 0 10px 30px rgba(0,0,0,.45);
  }
  .card--front { background: var(--black); }
  .card--back { background: var(--white); }

  .wordmark {
    font-family: "Lato", sans-serif;
    font-weight: 400;
    text-transform: uppercase;
    letter-spacing: .02em;
    display: flex;
    align-items: center;
    gap: 12px;
    white-space: nowrap;
  }
  .wordmark__dot {
    width: 20px; height: 20px; border-radius: 50%;
    background: var(--green-light);
  }
  .card--front .wordmark {
    position: absolute; left: 0; right: 0; top: 150px;
    justify-content: center;
    font-size: 30px; color: var(--white);
  }
  .card--front .web {
    position: absolute; left: 0; right: 0; bottom: 40px;
    text-align: center;
    font-family: "Work Sans", sans-serif;
    font-size: 17px; color: var(--white); letter-spacing: .03em;
  }
  .web__domain { color: var(--green-light); }
  .contact .web__domain { color: var(--green); }

  .card--back .wordmark {
    position: absolute; left: 0; right: 0; top: 50px;
    justify-content: center;
    font-size: 32px; color: var(--ink);
  }
  .details {
    position: absolute; left: 20px; right: 20px; top: 165px;
    display: flex; align-items: center; justify-content: center;
  }
  .provider { text-align: right; padding-right: 22px; white-space: nowrap; }
  .provider__name {
    font-family: "Oswald", sans-serif; font-weight: 500;
    font-size: 24px; color: var(--green); text-transform: uppercase;
    line-height: 1.15;
  }
  .provider__role {
    font-family: "Work Sans", sans-serif; font-size: 15px; color: var(--grey);
  }
  .divider { width: 1px; height: 70px; background: var(--green); flex: none; }
  .contact {
    list-style: none; padding-left: 22px; white-space: nowrap;
    font-family: "Work Sans", sans-serif; font-size: 16px; color: var(--ink);
    line-height: 1.5;
  }
  .contact li { display: flex; align-items: center; gap: 11px; }
  .contact svg { width: 13px; height: 13px; flex: none; }
  .address {
    position: absolute; left: 0; right: 0; bottom: 50px; text-align: center;
    font-family: "Work Sans", sans-serif; font-size: 19px; color: var(--ink);
    letter-spacing: .02em;
  }
</style>
</head>
<body>

  <section class="card card--front">
    <div class="wordmark"><span class="wordmark__dot"></span>Tolvera Hearing Center</div>
    <p class="web">www.<span class="web__domain">tolverahearing</span>.com</p>
  </section>

  <section class="card card--back">
    <div class="wordmark"><span class="wordmark__dot"></span>Tolvera Hearing Center</div>

    <div class="details">
      <div class="provider">
        <p class="provider__name">Peter Wolstenby, Au.D. F/NSB</p>
        <p class="provider__role">Owner-Audiologist</p>
      </div>
      <div class="divider"></div>
      <ul class="contact">
        <li>
          <svg viewBox="0 0 16 16" aria-hidden="true"><path d="M4 1l3 3-2 2c1 2 3 4 5 5l2-2 3 3-2 3C7 15 1 9 1 3z" fill="none" stroke="#6ea532" stroke-width="1.4"/></svg>
          (440) 683-5127
        </li>
        <li>
          <svg viewBox="0 0 16 16" aria-hidden="true"><rect x="1" y="3" width="14" height="10" fill="none" stroke="#6ea532" stroke-width="1.4"/><path d="M1 3l7 6 7-6" fill="none" stroke="#6ea532" stroke-width="1.4"/></svg>
          tolverahearing@postvane.com
        </li>
        <li>
          <svg viewBox="0 0 16 16" aria-hidden="true"><circle cx="8" cy="8" r="6.5" fill="none" stroke="#6ea532" stroke-width="1.3"/><ellipse cx="8" cy="8" rx="3" ry="6.5" fill="none" stroke="#6ea532" stroke-width="1.1"/><path d="M1.5 8h13" stroke="#6ea532" stroke-width="1.1"/></svg>
          <span>www.<span class="web__domain">tolverahearing</span>.com</span>
        </li>
      </ul>
    </div>

    <p class="address">837 W. Lindell Ave. Bellmont Falls, OH 44871</p>
  </section>

</body>
</html>
```